BRISK requires an exciting new business card

New business card required for BRISK. We are a new market research consultancy and want our brand to be approachable and be contemporary/modern, bold, uncomplicated/simple, and use friendly and easy to read fonts.

A draft website front page is attached to give you a feel (the pictures will be improved over the coming days).

The business card will be printed on 600gsm card, full colour both sides. The card is unique in that it allows one of four colours to be placed within the seam of the card (see http://uk.prentvo.com/products/gilt/business-cards.html)

The logo has been designed in yellow on white, white on yellow, yellow on black and black on yellow - please select whichever you feel most appropriate from the attached document (please use the versions with the tagline). I think my preference is yellow on white for the front, and then yellow or black as the dominant colour on the back.

Telephone numbers will be given next week as they are now being finalised.

Thanks

Target Market(s)

Professionals in large corporates, such as Marketing Managers at Grovane, Fizzaro Pop, Delmarco etc.

Industry/Entity Type

Market Research

Requirements
Must have
• Dana Pruitt QPMR
brisk
Level 4, 37 Quarrell St
Kellbrook Vale
NSW 2143
Tel: 02 XXXX XXXX
Mob: XXXX XXXXXX
Email: dana@briskqr.com.au
Web: www.briskqr.com.au

```html
<!DOCTYPE html>
<html lang="en">
<head>
<meta charset="utf-8">
<title>BRISK business card</title>
<link rel="stylesheet" href="https://fonts.googleapis.com/css2?family=Montserrat:wght@400;700&display=swap">
<style>
  :root {
    --brisk-yellow: #fdcb46;
    --accent-yellow: #f8c63f;
    --ink: #3d3d3d;
    --muted: #8c8c8c;
    --stage-light: #ffffff;
    --stage-edge: #e9e9e9;
    --paper: #ffffff;
  }
  * { margin: 0; padding: 0; box-sizing: border-box; }
  html, body { width: 1200px; height: 900px; overflow: hidden; }
  body {
    position: relative;
    background: var(--paper);
    font-family: "Montserrat", sans-serif;
  }
  .presentation-stage {
    position: absolute; left: 0; top: 0; width: 1200px; height: 695px;
    background: radial-gradient(ellipse 620px 380px at 600px 360px, var(--stage-light) 55%, var(--stage-edge) 100%);
  }
  .card { position: absolute; top: 220px; width: 449px; height: 256px; }
  .card-front {
    left: 125px; background: var(--brisk-yellow);
    display: flex; align-items: center; justify-content: center;
  }
  .card-back {
    left: 621px; background: var(--paper);
    box-shadow: 0 1px 4px rgba(0,0,0,0.22);
  }
  .wordmark {
    color: var(--ink); font-weight: 700; line-height: 1; letter-spacing: -0.5px;
  }
  .card-front .wordmark { font-size: 46px; margin-top: -6px; }

  .holder-badge {
    position: absolute; left: 47px; top: 38px; width: 72px; height: 72px;
    border-radius: 50%; background: var(--accent-yellow);
  }
  .holder-name {
    position: absolute; left: 133px; top: 55px;
    color: var(--accent-yellow); font-weight: 400; font-size: 21px; letter-spacing: 0.3px;
  }
  .holder-title {
    position: absolute; left: 133px; top: 80px;
    color: var(--accent-yellow); font-weight: 400; font-size: 14px; letter-spacing: 0.3px;
  }
  .contact-list, .address {
    position: absolute; top: 143px; list-style: none; font-style: normal;
    font-size: 12px; font-weight: 400; color: var(--muted); line-height: 19px;
  }
  .contact-list { left: 47px; }
  .contact-list li { display: flex; align-items: center; gap: 12px; }
  .contact-list svg { width: 14px; height: 14px; fill: var(--accent-yellow); flex: none; }
  .address { left: 263px; }

  .brand-signoff { position: absolute; left: 864px; top: 760px; font-size: 76px; }
</style>
</head>
<body>
  <div class="presentation-stage">
    <section class="card card-front">
      <span class="wordmark">brisk</span>
    </section>

    <section class="card card-back">
      <div class="holder-badge"></div>
      <p class="holder-name">DANA PRUITT</p>
      <p class="holder-title">QPMR</p>
      <ul class="contact-list">
        <li><svg viewBox="0 0 16 16"><path d="M3.5 1.5l2.5 3-1.5 1.8c.8 1.8 2.4 3.4 4.2 4.2l1.8-1.5 3 2.5-1.5 2.5C6.5 14 2 9.5 1 3z"/></svg>02 XXXX XXXX</li>
        <li><svg viewBox="0 0 16 16"><path d="M5 1h1v2h4a1 1 0 011 1v10a1 1 0 01-1 1H6a1 1 0 01-1-1zM7 5v3h3V5z"/></svg>XXXX XXXXXX</li>
        <li><svg viewBox="0 0 16 16"><path d="M1 4h14v1L8 9 1 5zM1 6.5l7 4 7-4V13H1z"/></svg>dana@briskqr.com.au</li>
        <li><svg viewBox="0 0 16 16"><path d="M8 1a7 7 0 100 14A7 7 0 008 1zm0 1.5c.8 1 1.4 2.6 1.6 4H6.4C6.6 5.1 7.2 3.5 8 2.5zM2.6 7.5h2.3c.1 1.4.5 2.8 1.1 3.9A5.5 5.5 0 012.6 7.5zm8.5 0h2.3a5.5 5.5 0 01-3.4 3.9c.6-1.1 1-2.5 1.1-3.9zM6.4 8.5h3.2c-.2 1.4-.8 3-1.6 4-.8-1-1.4-2.6-1.6-4z"/></svg>www.briskqr.com.au</li>
      </ul>
      <address class="address">
        brisk<br>
        Level 4, 37 Quarrell St<br>
        Kellbrook Vale<br>
        NSW 2143
      </address>
    </section>
  </div>

  <span class="brand-signoff wordmark">brisk</span>
</body>
</html>
```